Email Signature Block Design for Law Firm

I would like you to create a similar signature block for my law firm . I saw the email signature block attached as image002.png and wanted a similar design for my law firm. I want to be able to swap the portraits for each of my staff from the final design. Our law firm colors are black, gold, white, red.

Industry/Entity Type

Law

Requirements
Nice to have
• i like the red circle in around the photo in the tall oak group design. The Silver Lark Co desgn is what inspired me to have a signature block design for my firm.

```html
<!DOCTYPE html>
<html lang="en">
<head>
<meta charset="utf-8">
<title>The Harlow Firm – Email Signature</title>
<link href="https://fonts.googleapis.com/css2?family=Cinzel:wght@600&family=Poppins:wght@400;700&family=Roboto:wght@400&display=swap" rel="stylesheet">
<style>
  :root {
    --black: #000000;
    --white: #ffffff;
    --gold: #d9a231;
    --red: #d40d0d;
    --ink: #1a1a1a;
    --backdrop: #e4e4e4;
  }
  * { margin: 0; padding: 0; box-sizing: border-box; }
  html, body { width: 1200px; height: 600px; overflow: hidden; background: var(--backdrop); }
  .signature {
    position: absolute; left: 75px; top: 169px;
    width: 1051px; height: 247px;
    background: var(--white);
    font-family: 'Poppins', sans-serif;
    color: var(--ink);
  }
  .signature__band {
    position: absolute; left: 0; top: 0; width: 100%; height: 133px;
    background: var(--black);
  }
  .brand { position: absolute; left: 40px; top: 52px; display: flex; align-items: center; gap: 14px; }
  .brand__square { width: 58px; height: 58px; background: var(--gold); }
  .brand__name {
    font-family: 'Cinzel', serif; font-weight: 600; font-size: 24px;
    color: var(--white); letter-spacing: 0.5px; line-height: 1;
  }
  .brand__tagline {
    display: flex; align-items: center; gap: 6px; margin-top: 8px;
    font-family: 'Poppins', sans-serif; font-weight: 700; font-size: 10px;
    letter-spacing: 7px; color: var(--white); text-transform: none;
  }
  .brand__tagline::before, .brand__tagline::after {
    content: ""; display: block; width: 36px; height: 1px; background: var(--white);
  }
  .address {
    position: absolute; left: 40px; top: 156px;
    display: flex; align-items: center; gap: 6px; font-size: 13px;
  }
  .follow { position: absolute; left: 41px; top: 195px; display: flex; align-items: center; }
  .follow__label {
    font-weight: 700; font-size: 18px; letter-spacing: 2.2px; color: var(--red);
    margin-right: 16px;
  }
  .follow__dot { width: 20px; height: 20px; border-radius: 50%; background: var(--gold); margin-right: 19px; }
  .portrait {
    position: absolute; left: 432px; top: 98px; width: 186px; height: 186px;
    margin-top: -80px;
    border-radius: 50%; border: 8px solid var(--red);
    background: radial-gradient(circle at 50% 35%, #f4f4f4 0%, #e9e9e9 45%, #2a2a2a 46%, #111 100%);
  }
  .person { position: absolute; left: 661px; top: 52px; }
  .person__name {
    font-family: 'Cinzel', serif; font-weight: 600; font-size: 27px;
    color: var(--red); line-height: 1;
  }
  .person__title {
    font-family: 'Roboto', sans-serif; font-size: 16px; color: var(--white);
    margin-top: 6px; padding-bottom: 7px; width: 270px;
    border-bottom: 1px solid var(--red);
  }
  .contact { position: absolute; left: 661px; top: 142px; font-size: 14px; }
  .contact__row { display: flex; align-items: center; gap: 8px; height: 24px; }
  .contact__web {
    margin-top: 8px; font-size: 18px; letter-spacing: 5.2px; color: var(--ink);
  }
  .contact__web strong { color: var(--red); font-weight: 700; }
</style>
</head>
<body>
  <div class="signature">
    <div class="signature__band"></div>

    <div class="brand">
      <div class="brand__square"></div>
      <div>
        <div class="brand__name">The Harlow Firm, PLLC</div>
        <div class="brand__tagline">Attorneys At Law</div>
      </div>
    </div>

    <div class="address">
      <svg width="10" height="12" viewBox="0 0 10 12" aria-hidden="true">
        <path d="M5 0a5 5 0 0 1 5 5c0 3-5 7-5 7S0 8 0 5a5 5 0 0 1 5-5z" fill="var(--gold)"/>
        <circle cx="5" cy="5" r="1.8" fill="var(--white)"/>
      </svg>
      412 Elm Harbor St., Suite 310, Kestrel Bay, FL 32014
    </div>

    <div class="follow">
      <span class="follow__label">FOLLOW US ON</span>
      <span class="follow__dot"></span>
      <span class="follow__dot"></span>
      <span class="follow__dot"></span>
      <span class="follow__dot"></span>
      <span class="follow__dot"></span>
    </div>

    <div class="portrait" role="img" aria-label="Staff portrait: attorney in dark suit, arms crossed"></div>

    <div class="person">
      <div class="person__name">Marcus D. Harlow</div>
      <div class="person__title">PERSONAL INJURY LAWYER</div>
    </div>

    <div class="contact">
      <div class="contact__row">
        <svg width="11" height="11" viewBox="0 0 11 11" aria-hidden="true">
          <circle cx="5.5" cy="5.5" r="5.5" fill="var(--gold)"/>
          <path d="M3.3 2.8l1 .1.5 1.3-.6.5a4 4 0 0 0 1.9 1.9l.5-.6 1.3.5.1 1c-2.6.4-5-2-4.7-4.7z" fill="var(--white)"/>
        </svg>
        555-014-2288
      </div>
      <div class="contact__row">
        <svg width="11" height="11" viewBox="0 0 11 11" aria-hidden="true">
          <circle cx="5.5" cy="5.5" r="5.5" fill="var(--gold)"/>
          <rect x="2.8" y="3.6" width="5.4" height="3.8" fill="none" stroke="var(--white)" stroke-width="0.8"/>
          <path d="M2.8 3.6l2.7 2 2.7-2" fill="none" stroke="var(--white)" stroke-width="0.8"/>
        </svg>
        marcus@harlowfirm.com
      </div>
      <div class="contact__web">www.<strong>harlowfirm</strong>.com</div>
    </div>
  </div>
</body>
</html>
```